General contractor/GM consaltant business card

I need a card for my contracting company in North Dakota, we build industrial buildings for the oil feild and oil feild related companies offices, shops, airplain hangars, airports ext. We have a familly atmosphere on the job and are very relational and personal.
Industry/Entity Type
Industrial
Contact Information for Business Card
Ridgepost Contractors LLC.
Derek T.Holloway
4837 Tamarind dr. Colorado Springs, CO. 80917
Cell# 406-555-0148
derek@ridgepostcontractors.com

```html
<!DOCTYPE html>
<html lang="en">
<head>
<meta charset="utf-8">
<title>Ridgepost Contractors LLC. – Business Card</title>
<link rel="stylesheet" href="https://fonts.googleapis.com/css2?family=Arimo:wght@400;700&display=swap">
<style>
  :root {
    --page: #e9e6e1;
    --card-white: #ffffff;
    --card-black: #050505;
    --brand-red: #d4232f;
    --text-light: #f2f2f2;
    --shadow: rgba(0, 0, 0, 0.25);
  }
  * { box-sizing: border-box; margin: 0; padding: 0; }
  html, body {
    width: 1200px;
    height: 885px;
    overflow: hidden;
    background: var(--page);
    font-family: "Arimo", Arial, sans-serif;
  }
  .sheet {
    width: 1200px;
    height: 885px;
    display: flex;
    flex-direction: column;
    align-items: center;
    justify-content: center;
    gap: 45px;
  }
  .card {
    position: relative;
    width: 700px;
    height: 400px;
    border-radius: 28px;
    overflow: hidden;
    background: var(--card-white);
    box-shadow: 0 10px 28px var(--shadow);
  }
  .card__brand {
    position: absolute;
    left: 0;
    right: 0;
    top: 0;
    height: 220px;
    display: flex;
    align-items: flex-end;
    justify-content: center;
    padding-bottom: 22px;
  }
  .brand-name {
    color: var(--brand-red);
    font-weight: 700;
    font-size: 44px;
    letter-spacing: 0.2px;
    white-space: nowrap;
  }
  .card__band {
    position: absolute;
    left: 0;
    right: 0;
    bottom: 0;
    height: 180px;
    background: var(--card-black);
    color: var(--text-light);
  }
  .holder-name {
    position: absolute;
    left: 48px;
    bottom: 44px;
    font-size: 34px;
    font-weight: 400;
    letter-spacing: 0.3px;
  }
  .contact {
    position: absolute;
    right: 44px;
    top: 28px;
    list-style: none;
    text-align: right;
    font-size: 19px;
    line-height: 1.45;
  }
  .card--back .holder-name {
    left: 48px;
    bottom: 64px;
  }
</style>
</head>
<body>
  <main class="sheet">
    <section class="card card--front" aria-label="Business card front">
      <div class="card__brand">
        <span class="brand-name">Ridgepost Contractors LLC.</span>
      </div>
      <div class="card__band">
        <p class="holder-name">Derek T.Holloway</p>
        <ul class="contact">
          <li>406-555-0148</li>
          <li>derek@ridgepostcontractors.com</li>
          <li>4837 Tamarind dr.</li>
          <li>Colorado Springs, CO. 80917</li>
        </ul>
      </div>
    </section>

    <section class="card card--back" aria-label="Business card back">
      <div class="card__brand">
        <span class="brand-name">Ridgepost Contractors LLC.</span>
      </div>
      <div class="card__band">
        <p class="holder-name">Derek T.Holloway</p>
      </div>
    </section>
  </main>
</body>
</html>
```